Request for Business Card Design

Hi. My name is Marlene, I am looking for a new business card design for my company, Quarrow Signal Instruments, LLC. I really like the design you did for Tarsel Venture and was hoping you could do something similar using our full logo and our mark. I am also open to any raised texture design using our mark. I have attached our full logo, which would need to be somewhere on the card, as well as the mark in both outline and full form, as well as our brand colors / guide. The card does not have to be white, as long as our logo and mark appear. I actually like darker colored business cards more, but am open to all options. If you are interested in working with me, please let me know. We would also take the business card design into letterhead design if you can do that.

```html
<!DOCTYPE html>
<html lang="en">
<head>
<meta charset="utf-8">
<title>Quarrow Signal Instruments – Business Card</title>
<link rel="stylesheet" href="https://fonts.googleapis.com/css2?family=Open+Sans:wght@400;600;700;800&display=swap">
<style>
  :root {
    --stage: #2a2a2c;
    --card: #1b1b1d;
    --ink: #ffffff;
    --ink-soft: #e6e6e6;
    --accent: #0e9cc4;
  }
  html, body {
    margin: 0;
    padding: 0;
    width: 1200px;
    height: 900px;
    overflow: hidden;
    background: var(--stage);
    font-family: "Open Sans", Arial, sans-serif;
  }
  .stage {
    width: 1200px;
    height: 900px;
    display: flex;
    align-items: center;
    justify-content: center;
  }
  .card {
    position: relative;
    width: 900px;
    height: 514px;
    background: var(--card);
    border-bottom: 6px solid var(--accent);
    box-shadow: 0 24px 60px rgba(0,0,0,0.5);
    overflow: hidden;
  }
  .brand {
    position: absolute;
    left: 300px;
    top: 52px;
    color: var(--ink);
    font-weight: 800;
    line-height: 1;
  }
  .brand__name {
    font-size: 50px;
    letter-spacing: 4px;
    margin: 0;
  }
  .brand__tagline {
    font-size: 15px;
    letter-spacing: 1.5px;
    margin: 6px 0 0 2px;
  }
  .holder {
    position: absolute;
    left: 70px;
    top: 150px;
    padding-left: 40px;
  }
  .holder::before {
    content: "";
    position: absolute;
    left: 0;
    top: 2px;
    width: 20px;
    height: 40px;
    background: var(--accent);
  }
  .holder__name {
    margin: 0;
    color: var(--accent);
    font-size: 34px;
    font-weight: 700;
    letter-spacing: 0.5px;
    line-height: 1.1;
  }
  .holder__role {
    margin: 2px 0 0;
    color: var(--ink-soft);
    font-size: 20px;
  }
  .address {
    position: absolute;
    left: 110px;
    top: 250px;
    margin: 0;
    color: var(--ink-soft);
    font-size: 20px;
    font-style: normal;
    line-height: 1.35;
  }
  .contacts {
    position: absolute;
    left: 70px;
    top: 340px;
    margin: 0;
    padding: 0;
    list-style: none;
    color: var(--ink-soft);
    font-size: 20px;
    line-height: 1.4;
  }
  .contacts li {
    display: flex;
    align-items: center;
    gap: 14px;
  }
  .contacts svg {
    width: 18px;
    height: 18px;
    fill: var(--accent);
    flex: none;
  }
  .accent-disc {
    position: absolute;
    right: 70px;
    bottom: 40px;
    width: 300px;
    height: 300px;
    border-radius: 50%;
    background: var(--accent);
  }
</style>
</head>
<body>
<main class="stage">
  <section class="card" aria-label="Business card front">
    <header class="brand">
      <p class="brand__name">QUARROW</p>
      <p class="brand__tagline">SIGNAL INSTRUMENTS</p>
    </header>

    <div class="holder">
      <h1 class="holder__name">DANA WHITLOCK</h1>
      <p class="holder__role">Managing Director</p>
    </div>

    <address class="address">Your address, City<br>State, Zip 1234</address>

    <ul class="contacts">
      <li>
        <svg viewBox="0 0 24 24" aria-hidden="true"><path d="M6.6 10.8a15.1 15.1 0 0 0 6.6 6.6l2.2-2.2a1 1 0 0 1 1-.25 11.4 11.4 0 0 0 3.6.57 1 1 0 0 1 1 1V20a1 1 0 0 1-1 1A17 17 0 0 1 3 4a1 1 0 0 1 1-1h3.5a1 1 0 0 1 1 1c0 1.25.2 2.45.57 3.6a1 1 0 0 1-.25 1z"/></svg>
        123 456 789
      </li>
      <li>
        <svg viewBox="0 0 24 24" aria-hidden="true"><path d="M2 5h20v14H2z M2 5l10 8 10-8" /></svg>
        info@yourgmail.com
      </li>
      <li>
        <svg viewBox="0 0 24 24" aria-hidden="true"><circle cx="12" cy="12" r="10"/></svg>
        www.yourwebsite.com
      </li>
    </ul>

    <div class="accent-disc" aria-hidden="true"></div>
  </section>
</main>
</body>
</html>
```